Brevlon Website Design - Wordpress

Need a website WordPress design for our existing website that we just stood up. The logo is already in place and name. Brevlon.example We are a company which makes connections with our clients through educating them and providing networking events. We would like for the website to show a VIP/special feel to it.

Target Market(s)

Business executives and employees. Age group 26-65 in the following sectors:
- Technology
- Human Resources
- Finance
- Sales

Industry/Entity Type

Technical Service

Number of Pages Required

4 page

Font styles to use
Sans Serif

Requirements
Must have
• Must be something for Wordpress
Nice to have
• Would like this to be professional but look cutting edge and VIP.

```html
<!DOCTYPE html>
<html lang="en">
<head>
<meta charset="utf-8">
<title>Brevlon — Expand Your Business</title>
<link rel="stylesheet" href="https://fonts.googleapis.com/css2?family=Arimo:wght@400;700&family=Open+Sans:wght@400;600&display=swap">
<style>
  :root {
    --ink: #ffffff;
    --muted: #d8d8d8;
    --black: #000000;
    --footer: #1b1b1b;
    --red: #b5141b;
    --crimson: #a0101c;
    --purple: #5e2a7a;
    --blue: #1b5b95;
    --gold: #e2a51c;
    --card: rgba(90, 0, 25, 0.42);
    --line: #e6e6e6;
  }
  * { box-sizing: border-box; margin: 0; padding: 0; }
  html, body { width: 1200px; height: 2528px; overflow: hidden; background: var(--black); }
  body { position: relative; font-family: "Open Sans", sans-serif; color: var(--ink); }
  .heading { font-family: "Arimo", sans-serif; font-weight: 400; text-transform: uppercase; }
  .abs { position: absolute; }
  .center { left: 0; width: 1200px; text-align: center; }
  .pill {
    position: absolute; display: flex; align-items: center; justify-content: center;
    border-radius: 26px; font-family: "Arimo", sans-serif; font-weight: 700; font-size: 19px;
    color: var(--ink); text-transform: uppercase;
  }

  /* Hero */
  .hero { position: absolute; left: 0; top: 0; width: 1200px; height: 679px;
    background: linear-gradient(180deg, #2a2926 0%, #5a5650 38%, #3e3b36 62%, #24221f 100%); }
  .brand { position: absolute; left: 162px; top: 34px; display: flex; align-items: center; gap: 14px; }
  .brand-mark { width: 34px; height: 34px; background: var(--ink); }
  .brand-name { font-family: "Arimo", sans-serif; font-size: 34px; letter-spacing: 5px; color: var(--ink); }
  .nav { position: absolute; top: 42px; display: flex; gap: 0; }
  .nav a { color: var(--ink); text-decoration: none; font-family: "Arimo", sans-serif; font-size: 17px; }
  .main-nav { left: 585px; }
  .main-nav a { margin-right: 44px; }
  .hero-title { top: 260px; font-size: 58px; }
  .hero-sub { top: 336px; font-size: 34px; }
  .hero-btn { left: 502px; top: 398px; width: 196px; height: 47px; background: var(--red); }
  .dots { position: absolute; left: 573px; top: 623px; display: flex; gap: 8px; }
  .dots span { width: 17px; height: 17px; border-radius: 50%; border: 2px solid var(--ink); }
  .dots .on { background: var(--ink); }

  /* Strategy */
  .strategy-title { top: 774px; font-size: 35px; }
  .strategy-text { top: 823px; font-size: 21px; line-height: 31px; color: var(--muted); }
  .diagram { position: absolute; left: 177px; top: 918px; width: 857px; height: 281px; }

  /* Offer */
  .offer { position: absolute; left: 0; top: 1326px; width: 1200px; height: 556px;
    background: linear-gradient(120deg, var(--red) 0%, #8e1a3d 50%, var(--purple) 100%); }
  .offer-title { top: 58px; font-size: 33px; }
  .card { position: absolute; width: 207px; height: 277px; background: var(--card);
    display: flex; flex-direction: column; align-items: center; padding: 18px 14px 0; text-align: center; }
  .card svg { width: 64px; height: 64px; }
  .card h3 { font-family: "Arimo", sans-serif; font-weight: 700; font-size: 19px; margin-top: 4px; }
  .card p { font-size: 13px; line-height: 21.5px; margin-top: 6px; color: #f1e3e7; }
  .value-btn { left: 526px; top: 458px; width: 173px; height: 44px; background: var(--gold); }

  /* Contact */
  .contact { position: absolute; left: 0; top: 1882px; width: 1200px; height: 457px;
    background: linear-gradient(100deg, #202124 0%, #2c2e33 45%, #1d1f24 100%); }
  .contact-title { top: 68px; font-size: 31px; }
  .field { position: absolute; border-bottom: 2px solid var(--line); font-size: 16px; padding-bottom: 6px; color: var(--ink); }
  .submit-btn { left: 527px; top: 325px; width: 172px; height: 46px; background: var(--purple); }

  /* Footer */
  .footer { position: absolute; left: 0; top: 2339px; width: 1200px; height: 189px; background: var(--footer); }
  .foot-nav { left: 398px; top: 39px; }
  .foot-nav a { margin-right: 44px; }
  .copyright { top: 71px; font-size: 13px; color: var(--muted); }
  .social { position: absolute; left: 524px; top: 106px; display: flex; gap: 5px; }
  .social span { width: 33px; height: 33px; border-radius: 50%; border: 2px solid var(--ink); }
</style>
</head>
<body>

<header class="hero" role="img" aria-label="Photo of a desert road stretching to the horizon with the words grow your business painted on it">
  <div class="brand"><span class="brand-mark"></span><span class="brand-name">BREVLON</span></div>
  <nav class="nav main-nav"><a href="#">EVENTS</a><a href="#">EXPAND</a><a href="#">ABOUT</a><a href="#">CONNECT</a></nav>
  <h1 class="abs center heading hero-title">Expand Your Business</h1>
  <p class="abs center heading hero-sub">Donec Convallis Pede Venenat</p>
  <a class="pill hero-btn">Read More</a>
  <div class="dots"><span></span><span class="on"></span><span></span></div>
</header>

<section class="strategy">
  <h2 class="abs center heading strategy-title">It's About Our Unique X Strategy</h2>
  <p class="abs center strategy-text">BREVLON provides impactful connection opportunities to help educate,<br>equip and expand you and your business</p>

  <svg class="diagram" viewBox="105 545 509 167" aria-label="Four parts of the strategy: mind, heart, soul and strength">
    <g fill="none" stroke-width="1.4">
      <polygon points="105,552 283,552 322,625 128,625" stroke="var(--blue)"/>
      <polygon points="128,632 322,632 283,704 107,704" stroke="var(--purple)"/>
      <polygon points="430,552 606,552 583,625 390,625" stroke="var(--red)"/>
      <polygon points="390,632 583,632 606,704 430,704" stroke="var(--gold)"/>
      <circle cx="356" cy="628" r="26" stroke="#5a5a5a"/>
    </g>
    <g fill="none" stroke-width="1.6" stroke-linecap="round" stroke-linejoin="round">
      <circle cx="256" cy="586" r="11" stroke="var(--blue)"/>
      <path d="M240 596 v10 h8 M272 596 v10 h-8 M256 580 v12 M250 586 h12" stroke="var(--blue)"/>
      <path d="M455 600 l-16 -15 a8 8 0 0 1 16 -8 a8 8 0 0 1 16 8 z" stroke="var(--red)"/>
      <path d="M433 590 h10 l4 -6 l5 12 l4 -6 h22" stroke="var(--red)"/>
      <path d="M240 682 v-14 a16 16 0 1 1 28 8 v8 h-8" stroke="var(--purple)"/>
      <circle cx="254" cy="664" r="6" stroke="var(--purple)"/>
      <circle cx="458" cy="664" r="17" stroke="var(--gold)"/>
      <path d="M461 651 l-8 14 h9 l-6 13" stroke="var(--gold)"/>
    </g>
    <g font-family="Open Sans, sans-serif" text-anchor="end">
      <text x="207" y="582" font-size="14" fill="var(--blue)">MIND</text>
      <text x="207" y="598" font-size="11" fill="#ffffff">THOUGHT</text>
      <text x="207" y="665" font-size="14" fill="var(--purple)">SOUL</text>
      <text x="207" y="681" font-size="11" fill="#ffffff">INTUTION</text>
    </g>
    <g font-family="Open Sans, sans-serif">
      <text x="485" y="586" font-size="14" fill="var(--red)">HEART</text>
      <text x="485" y="602" font-size="11" fill="#ffffff">EMOTIONS</text>
      <text x="485" y="665" font-size="14" fill="var(--gold)">STRENGTH</text>
      <text x="485" y="681" font-size="11" fill="#ffffff">ENERGY</text>
    </g>
  </svg>
</section>

<section class="offer">
  <h2 class="abs center heading offer-title">What We Offer You</h2>

  <article class="card" style="left:162px; top:125px;">
    <svg viewBox="0 0 64 64" fill="none" stroke="#fff" stroke-width="2" stroke-linecap="round"><path d="M24 38 a12 12 0 1 1 16 0 v6 h-16 z M26 49 h12 M28 53 h8 M32 8 v5 M14 16 l4 4 M50 16 l-4 4 M8 32 h5 M56 32 h-5"/></svg>
    <h3>EDUCATE</h3>
    <p>At BREVLON, we provide effective training and learning as the foundation for building a healthy, successful company.</p>
  </article>

  <article class="card" style="left:389px; top:158px;">
    <svg viewBox="0 0 64 64" fill="none" stroke="#fff" stroke-width="2" stroke-linecap="round"><circle cx="32" cy="32" r="6"/><circle cx="14" cy="14" r="4"/><circle cx="50" cy="14" r="4"/><circle cx="14" cy="50" r="4"/><circle cx="50" cy="50" r="4"/><path d="M17 17 l11 11 M47 17 l-11 11 M17 47 l11 -11 M47 47 l-11 -11"/></svg>
    <h3>EQUIP</h3>
    <p>Through our connected ecosystem of companies, we'll help find the right partners for equipping you to move forward.</p>
  </article>

  <article class="card" style="left:625px; top:125px;">
    <svg viewBox="0 0 64 64" fill="none" stroke="#fff" stroke-width="2" stroke-linecap="round" stroke-linejoin="round"><path d="M8 20 h12 c10 0 14 24 24 24 h8 M8 44 h12 c4 0 7 -4 9 -8 M36 26 c2 -4 4 -6 8 -6 h8 M46 12 l8 8 l-8 8 M46 36 l8 8 l-8 8"/></svg>
    <h3>EXCHANGE</h3>
    <p>We connect you with others who have successfully implemented our X Strategy to facilitate growth in their business.</p>
  </article>

  <article class="card" style="left:853px; top:158px;">
    <svg viewBox="0 0 64 64" fill="none" stroke="#fff" stroke-width="2" stroke-linecap="round"><rect x="8" y="10" width="48" height="34"/><path d="M8 38 h48 M32 44 v8 M22 54 h20 M22 32 v-10 M28 32 v-14 M34 32 v-8 M40 32 v-12"/></svg>
    <h3>EXPAND</h3>
    <p>Our goal is to help you and your business increase productivity and scale through effective strategy and healthy culture.</p>
  </article>

  <a class="pill value-btn">X = Value</a>
</section>

<section class="contact" role="img" aria-label="Dim photo of colleagues working together in an office">
  <h2 class="abs center heading contact-title">Contact Form</h2>
  <div class="field" style="left:211px; top:154px; width:236px;">Your Name</div>
  <div class="field" style="left:480px; top:154px; width:236px;">Email address</div>
  <div class="field" style="left:750px; top:154px; width:236px;">Phone Number</div>
  <div class="field" style="left:211px; top:205px; width:775px; height:89px;">Write a message here</div>
  <a class="pill submit-btn">Submit</a>
</section>

<footer class="footer">
  <nav class="nav foot-nav"><a href="#">EVENTS</a><a href="#">EXPAND</a><a href="#">ABOUT</a><a href="#">CONNECT</a></nav>
  <p class="abs center copyright">© 2019 Company Name &nbsp;All right reserved</p>
  <div class="social"><span></span><span></span><span></span><span></span></div>
</footer>

</body>
</html>
```